Business card design for a dynamic IT consulting company

We need a business card design for a young firm, specialized in the Telecommunications/Consulting industry. The name of the company is Quindor and Partners Business Consulting Ltd. (Short name: Quindor and Partnes)
Quindor = solve read reverse, so we aim to be uncomplicated and solution-oriented. The small pipe in our logo is also related to the word solve. So we need a new business card design, which is simple, eye catching and something non traditional (I would probably prefer a square shaped design rather than a rectangle, but open for suggestions). Attached our logo.

Target Market(s)

Usually our customers are Tier1 Telecoms providers (Q-Netra, Palorix, etc) and their executives.

Industry/Entity Type

Business

Contact Information for Business Card

Name: Bence Tolnavari
Email: b.tolnavari@quindor.hu
Web: www.quindor.hu
Mobile: +36 30 518 2769
Title: Managing Director

Optional:
Company name: Quindor and Partners Ltd.
Address: 1087 Budapest, Tolvenka str. 28/C, Hungary

Font styles to use
Other font styles liked:
• helveticaneue_medium, Prime Regular are used now.

Colors

Designer to choose colors to be used in the design.

Requirements
Must have
• I would like to have a 2 sided design.
Nice to have
• I thought if we make the logo a bit bigger (without the company name), that could go to the back with the company name below. I though, if the pipe in the logo is somehow touchable on the business card, would be nice and unique.

```html
<!DOCTYPE html>
<html lang="en">
<head>
<meta charset="utf-8">
<title>Quindor and Partners – Business Card</title>
<link href="https://fonts.googleapis.com/css2?family=Exo+2:wght@400;500&family=Roboto:wght@400&display=swap" rel="stylesheet">
<style>
  :root {
    --stage: #2a2a2c;
    --card-dark: #5e5e60;
    --card-light: #ffffff;
    --ink: #5b5b5d;
    --ink-soft: #707072;
    --magenta: #b0217f;
    --cyan: #1e9ad6;
    --white: #ffffff;
  }
  * { box-sizing: border-box; margin: 0; padding: 0; }
  html, body { width: 1200px; height: 880px; overflow: hidden; }
  body { background: var(--stage); position: relative; font-family: "Roboto", Arial, sans-serif; }

  .card {
    position: absolute;
    width: 600px; height: 345px;
    border-radius: 22px;
    overflow: hidden;
    box-shadow: 0 18px 40px rgba(0,0,0,.45);
  }

  /* Back side */
  .card-back { left: 80px; top: 70px; background: var(--card-dark); }
  .back-brand {
    position: absolute; left: 0; right: 0; top: 128px;
    display: flex; justify-content: center; align-items: center; gap: 14px;
  }
  .brand-square { width: 16px; height: 16px; background: var(--magenta); flex: none; }
  .back-brand .brand-name {
    font-family: "Exo 2", sans-serif; font-weight: 400;
    font-size: 50px; color: var(--white); letter-spacing: .5px;
  }
  .back-web {
    position: absolute; left: 0; right: 0; top: 232px; text-align: center;
    font-size: 14px; letter-spacing: 3px; color: #e6e6e6;
  }

  /* Front side */
  .card-front { left: 520px; top: 465px; background: var(--card-light); }
  .front-brand {
    position: absolute; left: 40px; top: 40px;
    display: flex; align-items: center; gap: 16px;
  }
  .front-brand .brand-square { width: 26px; height: 26px; }
  .brand-pipe { width: 2px; height: 62px; background: var(--ink); }
  .front-brand .brand-name {
    font-family: "Exo 2", sans-serif; font-weight: 400;
    font-size: 54px; color: var(--ink); line-height: 1;
  }

  .divider { position: absolute; top: 222px; height: 2px; }
  .divider-left { left: 40px; width: 260px; background: var(--magenta); }
  .divider-right { left: 300px; width: 260px; background: var(--cyan); }

  .person { position: absolute; left: 40px; top: 166px; }
  .person-name {
    font-family: "Exo 2", sans-serif; font-weight: 500;
    font-size: 26px; color: var(--ink); line-height: 1;
  }
  .person-title {
    font-family: "Exo 2", sans-serif; font-weight: 400;
    font-size: 17px; color: var(--magenta); margin-top: 3px;
  }

  .contacts { position: absolute; left: 40px; top: 238px; list-style: none; }
  .contacts li {
    display: flex; align-items: center; gap: 9px;
    font-size: 15px; color: var(--ink-soft); height: 22px;
  }
  .contacts svg { width: 16px; height: 16px; flex: none; }

  .address { position: absolute; right: 40px; top: 234px; text-align: right; }
  .address-company {
    font-family: "Exo 2", sans-serif; font-weight: 500;
    font-size: 18px; color: var(--ink);
  }
  .address-line { font-size: 14px; color: var(--ink-soft); line-height: 1.4; }
</style>
</head>
<body>

<section class="card card-back" aria-label="Card back">
  <div class="back-brand">
    <span class="brand-square"></span>
    <span class="brand-name">Quindor &amp; Partners</span>
  </div>
  <p class="back-web">www.quindor.hu</p>
</section>

<section class="card card-front" aria-label="Card front">
  <div class="front-brand">
    <span class="brand-square"></span>
    <span class="brand-pipe"></span>
    <span class="brand-name">Quindor &amp; Partners</span>
  </div>

  <div class="person">
    <p class="person-name">Bence Tolnavari</p>
    <p class="person-title">Managing Director</p>
  </div>

  <span class="divider divider-left"></span>
  <span class="divider divider-right"></span>

  <ul class="contacts">
    <li>
      <svg viewBox="0 0 16 16" aria-hidden="true"><rect width="16" height="16" fill="#b0217f"/><rect x="5" y="3" width="6" height="10" rx="1" fill="none" stroke="#fff" stroke-width="1.3"/></svg>
      +36 30 518 2769
    </li>
    <li>
      <svg viewBox="0 0 16 16" aria-hidden="true"><rect width="16" height="16" fill="#5b5b5d"/><rect x="3" y="4.5" width="10" height="7" fill="none" stroke="#fff" stroke-width="1.2"/><path d="M3 4.5 8 9l5-4.5" fill="none" stroke="#fff" stroke-width="1.2"/></svg>
      b.tolnavari@quindor.hu
    </li>
    <li>
      <svg viewBox="0 0 16 16" aria-hidden="true"><rect width="16" height="16" fill="#1e9ad6"/><circle cx="8" cy="8" r="4.8" fill="none" stroke="#fff" stroke-width="1.1"/><path d="M3.2 8h9.6M8 3.2c-2.2 2.6-2.2 7 0 9.6M8 3.2c2.2 2.6 2.2 7 0 9.6" fill="none" stroke="#fff" stroke-width="1"/></svg>
      www.quindor.hu
    </li>
  </ul>

  <address class="address" style="font-style:normal">
    <p class="address-company">Quindor and Partners Ltd.</p>
    <p class="address-line">1087 Budapest</p>
    <p class="address-line">Tolvenka str. 28/C, Hungary</p>
  </address>
</section>

</body>
</html>
```